Building Referrer Relationships Booklet

4 page A4 booklet to give to potential professional referrers to establish a collaborative relationship.Needs to be bright, vibrant, colourful, friendly, inviting, in keeping with The Linden Practice colours.
Want to provide potential referrer partners a great reason to choose to collaborate with us. They need to know who we are, what makes us different/appealing, and who we are looking for to connect with.
The final product should communicate high performance and connectedness.
Updates

Target Market(s)

professional medical allied health and fitness practitioners

Industry/Entity Type

Health

Requirements
Must have
• energetic, vibrant, engaging, inviting, images

```html
<!DOCTYPE html>
<html lang="en">
<head>
<meta charset="utf-8">
<title>The Linden Practice – Referrer Booklet Spread</title>
<link rel="stylesheet" href="https://fonts.googleapis.com/css2?family=Questrial&family=Cinzel:wght@400;600&family=Crimson+Text:wght@400;600&display=swap">
<style>
:root{
  --bg:#e4e4e4;
  --paper:#ffffff;
  --orange:#f5b35a;
  --orange-deep:#e8662a;
  --teal:#3fbfae;
  --grey-band:#6b6c70;
  --ink:#3a3a3a;
  --ink-soft:#555;
  --red:#e0262b;
  --amber:#f3a61d;
  --green:#3aaa4a;
  --blue:#1c8fd6;
  --navy:#27307a;
  --yellow:#f3e61c;
}
*{box-sizing:border-box;margin:0;padding:0}
html,body{width:1200px;height:840px;overflow:hidden;background:var(--bg)}
body{font-family:"Questrial",sans-serif;color:var(--ink)}
.spread{position:absolute;left:40px;top:24px;width:1120px;height:792px;display:flex;box-shadow:0 10px 30px rgba(0,0,0,.18)}
.page{position:relative;width:560px;height:792px;background:var(--paper);overflow:hidden}
.page--left{border-right:1px solid #ddd}
.tab{position:absolute;background:var(--orange);color:#fff;font-family:"Cinzel",serif;font-weight:600;letter-spacing:1px;display:flex;align-items:center;justify-content:center}
.corner{position:absolute;width:60px;height:60px;background:linear-gradient(135deg,var(--orange-deep),#f08a3c)}
.corner--br{right:0;bottom:0;clip-path:polygon(100% 0,100% 100%,0 100%)}
.corner--tl{left:0;top:0;clip-path:polygon(0 0,100% 0,0 100%)}

/* About */
.about-tab{left:250px;top:0;width:170px;height:56px;font-size:18px}
.about-copy{position:absolute;left:140px;top:72px;width:330px;font-size:10.5px;line-height:1.45;text-align:justify;color:var(--ink-soft)}
.values{position:absolute;left:425px;top:262px;width:130px;height:142px}
.value{position:absolute;width:44px;height:44px;border-radius:50%;border:3px solid var(--orange-deep);box-shadow:0 0 0 2px #bbb;background:#fff;display:flex;align-items:center;justify-content:center;font-family:"Cinzel",serif;font-size:5.5px;color:#555}
.photo{position:absolute}
.photo--team-run{left:130px;top:262px;width:285px;height:228px;background:linear-gradient(160deg,#4d7a52 0%,#6aa36b 35%,#7fb0d8 70%,#5b93c9 100%)}
.clients-band{position:absolute;left:40px;top:420px;width:300px;height:74px;background:var(--grey-band);color:#fff;font-family:"Cinzel",serif;padding:10px 18px;text-align:center}
.clients-band__title{font-size:11px;letter-spacing:.5px;line-height:1.4}
.clients-band__title b{font-size:22px;font-weight:600;vertical-align:middle;margin:0 4px;line-height:1}
.clients-band__note{font-family:"Questrial",sans-serif;font-size:9px;font-style:italic;opacity:.85}
.loves{position:absolute;left:50px;top:508px;width:270px;list-style:none}
.loves li{position:relative;padding-left:26px;font-size:10.5px;line-height:1.4;color:var(--ink-soft);margin-bottom:10px}
.loves li::before{content:"";position:absolute;left:0;top:2px;width:14px;height:14px;background:
  linear-gradient(var(--teal),var(--teal)) 0 0/6px 6px no-repeat,
  linear-gradient(var(--teal),var(--teal)) 8px 0/6px 6px no-repeat,
  linear-gradient(var(--teal),var(--teal)) 0 8px/6px 6px no-repeat,
  linear-gradient(var(--teal),var(--teal)) 8px 8px/6px 6px no-repeat}
.quote{position:absolute;left:345px;top:515px;width:170px;color:var(--red);font-size:10px;line-height:1.35;text-transform:uppercase;text-align:center}
.quote__mark{font-family:"Cinzel",serif;font-size:34px;color:#222;line-height:0;position:relative;top:12px}
.team-title{position:absolute;font-family:"Cinzel",serif;font-size:28px;color:var(--blue);letter-spacing:1px;line-height:1}
.team-rule{position:absolute;height:1.5px;background:var(--blue)}
.member{position:absolute;width:96px;text-align:center}
.member__hex{width:80px;height:72px;margin:0 auto;clip-path:polygon(25% 0,75% 0,100% 50%,75% 100%,25% 100%,0 50%);display:flex;align-items:center;justify-content:center}
.member__photo{width:70px;height:62px;clip-path:polygon(25% 0,75% 0,100% 50%,75% 100%,25% 100%,0 50%);background:linear-gradient(180deg,#b9c4cf,#7d8a99)}
.member__name{font-family:"Crimson Text",serif;font-size:8.5px;font-weight:600;margin-top:4px;color:#333;line-height:1.2}
.member__role{font-family:"Crimson Text",serif;font-size:8px;color:#555;line-height:1.2}

/* Right page */
.way-title{position:absolute;left:30px;top:62px;width:250px;text-align:center;font-size:19px;letter-spacing:1px;line-height:1.2;color:#333}
.way-copy{position:absolute;left:30px;top:118px;width:250px;font-size:10.5px;line-height:1.4;text-align:justify;color:var(--ink-soft)}
.photo--workshop{left:28px;top:215px;width:260px;height:290px;background:linear-gradient(150deg,#b7704b 0%,#d29a6c 40%,#8e7b6a 70%,#c7482f 100%)}
.fix-tab{left:330px;top:60px;width:200px;height:50px;font-size:17px}
.pathway{position:absolute;left:305px;top:122px;width:240px}
.step{margin-bottom:6px}
.step__head{display:flex;align-items:baseline;gap:8px}
.step__num{font-size:24px;color:#333;font-weight:400}
.step__title{font-size:10px;text-transform:uppercase;letter-spacing:.5px}
.step__note{font-family:"Crimson Text",serif;font-size:7.5px;color:#666;margin:-3px 0 2px 38px}
.step ul{list-style:none;margin-left:16px}
.step li{position:relative;padding-left:14px;font-family:"Crimson Text",serif;font-size:10.5px;line-height:1.2;color:#333}
.step li::before{content:"";position:absolute;left:0;top:4px;width:7px;height:7px;background:
  linear-gradient(var(--teal),var(--teal)) 0 0/3px 3px no-repeat,
  linear-gradient(var(--teal),var(--teal)) 4px 0/3px 3px no-repeat,
  linear-gradient(var(--teal),var(--teal)) 0 4px/3px 3px no-repeat,
  linear-gradient(var(--teal),var(--teal)) 4px 4px/3px 3px no-repeat}
.t-red{color:var(--red)}.t-amber{color:var(--amber)}.t-green{color:var(--green)}.t-dark{color:#333}
.biohack{position:absolute;left:40px;top:520px;width:250px;height:34px}
.biohack__text{position:absolute;left:50px;top:9px;font-family:"Cinzel",serif;font-size:11px;color:#fff;letter-spacing:1px}
</style>
</head>
<body>
<main class="spread">

  <!-- Left page -->
  <section class="page page--left">
    <div class="tab about-tab">ABOUT US</div>
    <p class="about-copy">COURAGE gives us the strength and confidence to take risks and embrace challenges. INSPIRATION is our energy, our fuel for success, that life force that feeds us as we grow and develop. FUN generates happiness, and we all function at our best when we are happy. CREATIVITY sets us as an innovative leading-edge business. WOW means being the very best we can be and realise our true potential. We are not your average business, our service is not average, and our people are not average. TEAM and in particular high-performance team means we perform at our very best. Great teamwork creates unity and we accomplish much more than each of us alone.</p>

    <div class="photo photo--team-run" role="img" aria-label="Team of runners in national colours arm in arm on an athletics track"></div>

    <div class="values" aria-label="Our values">
      <div class="value" style="left:0;top:0">COURAGE</div>
      <div class="value" style="left:46px;top:22px">INSPIRATION</div>
      <div class="value" style="left:4px;top:48px">CREATIVE</div>
      <div class="value" style="left:80px;top:60px">FUN</div>
      <div class="value" style="left:44px;top:76px">WOW</div>
      <div class="value" style="left:8px;top:98px">TEAM</div>
    </div>

    <div class="clients-band">
      <div class="clients-band__title">THE TOP <b>3</b> THINGS OUR CLIENTS<br>LOVE ABOUT US</div>
      <div class="clients-band__note">(and hopefully yours will too!)</div>
    </div>

    <ul class="loves">
      <li>Positive energy, enthusiasm and outcomes NPS average score &gt;9 out of 10</li>
      <li>Trusted leader in the practice of podiatric medicine established 1999, elite experience, latest high-tech equipment</li>
      <li>Focus is on strong feet, not just orthotics! Barefoot Motion Method, Fascial Lines, Foot Manual Therapies</li>
    </ul>

    <p class="quote"><span class="quote__mark">“</span> At The Linden Practice we are passionate about building strong postural foundations, from the feet up. <span class="quote__mark">”</span></p>

    <div class="team-rule" style="left:350px;top:628px;width:150px"></div>
    <div class="team-title" style="left:476px;top:692px">OUR</div>

    <div class="member" style="left:205px;top:660px">
      <div class="member__hex" style="background:var(--teal)"><div class="member__photo" role="img" aria-label="Portrait of principal podiatrist"></div></div>
      <div class="member__name">Dr Ravi Anandakumar</div><div class="member__role">Principal Podiatrist</div>
    </div>
    <div class="member" style="left:295px;top:676px">
      <div class="member__hex" style="background:var(--green)"><div class="member__photo" role="img" aria-label="Portrait of senior podiatrist"></div></div>
      <div class="member__name">Dr Claire Whitford</div><div class="member__role">Senior Podiatrist</div>
    </div>
    <div class="member" style="left:385px;top:692px">
      <div class="member__hex" style="background:var(--yellow)"><div class="member__photo" role="img" aria-label="Portrait of podiatrist"></div></div>
      <div class="member__name">Dr Hannah Pereira</div><div class="member__role">Podiatrist</div>
    </div>

    <div class="corner corner--br"></div>
  </section>

  <!-- Right page -->
  <section class="page page--right">
    <div class="corner corner--tl"></div>
    <h2 class="way-title">THE<br>LINDEN PRACTICE WAY</h2>
    <p class="way-copy">Our pathway to strengthen postural foundations, to create lasting changes for freedom of movement, and ultimately keep us going well beyond what we thought was possible (updated as research and tech changes).</p>

    <div class="photo photo--workshop" role="img" aria-label="Collage of group workshop and movement class photos"></div>

    <div class="tab fix-tab">FIX YOUR FEET</div>

    <div class="pathway">
      <div class="step">
        <div class="step__head"><span class="step__num">01</span><span class="step__title t-red">Fix the pain</span></div>
        <ul><li>Provide analgesia</li><li>Reduce inflammation</li><li>Corn/callus/foreign body removal</li><li>Ingrown/thickened toenail repair and maintenance</li><li>Surgery</li></ul>
      </div>
      <div class="step">
        <div class="step__head"><span class="step__num">02</span><span class="step__title t-amber">Protect the feet</span></div>
        <div class="step__note">(reduce damage, optimise stability, promote healing)</div>
        <ul><li>Reduce tissue damage</li><li>Optimise Foot Posture</li><li>Activate neuromuscular/reflexive balance stability</li><li>Promote tissue repair/cellular regeneration</li></ul>
      </div>
      <div class="step">
        <div class="step__head"><span class="step__num">03</span><span class="step__title t-green">Strengthen the feet</span></div>
        <div class="step__note">(increase strength and resilience)</div>
        <ul><li>Strengthen intrinsics</li><li>Connect foot strength to core strength</li><li>Stimulate neuromuscular strength</li></ul>
      </div>
      <div class="step">
        <div class="step__head"><span class="step__num">04</span><span class="step__title t-green">Protect the whole body</span></div>
        <div class="step__note">(stability)</div>
        <ul><li>Optimise Postural Alignment</li><li>Activate neuromuscular/reflexive balance stability</li><li>Customised corrective exercises</li><li>Improve cellular regeneration</li><li>Optimise nutrition/healthy gut</li><li>Optimise healthy mind</li></ul>
      </div>
      <div class="step">
        <div class="step__head"><span class="step__num">05</span><span class="step__title t-green">Strengthen the whole body</span></div>
        <div class="step__note">(strength, elasticity)</div>
        <ul><li>Strengthen the deep core (stabilisers)</li><li>Strengthen the outer core (mobilisers)</li><li>Increase fascial elasticity/strength</li><li>Increase functional strength</li><li>Increase endurance</li><li>Customised nutrition for specific performance</li><li>Improve psychological resilience</li></ul>
      </div>
      <div class="step">
        <div class="step__head"><span class="step__num">06</span><span class="step__title t-dark">Repeat consistently</span></div>
      </div>
    </div>

    <div class="biohack">
      <svg width="250" height="34" viewBox="0 0 250 34" aria-hidden="true">
        <defs><linearGradient id="pill" x1="0" x2="1"><stop offset="0" stop-color="#5fb2e6"/><stop offset="1" stop-color="#1b6fb8"/></linearGradient></defs>
        <rect x="10" y="5" width="236" height="24" rx="12" fill="url(#pill)"/>
        <circle cx="22" cy="17" r="17" fill="#3a8fd0"/>
        <circle cx="22" cy="17" r="11" fill="#fff"/>
        <circle cx="22" cy="17" r="8" fill="none" stroke="#8cc6ee" stroke-width="2"/>
      </svg>
      <span class="biohack__text">BIOHACK YOUR BODY</span>
    </div>

    <div class="team-title" style="left:20px;top:566px">TEAM</div>
    <div class="team-rule" style="left:120px;top:582px;width:170px"></div>

    <div class="member" style="left:20px;top:612px">
      <div class="member__hex" style="background:var(--navy)"><div class="member__photo" role="img" aria-label="Portrait of podiatrist"></div></div>
      <div class="member__name">Dr Marcus Teo</div><div class="member__role">Podiatrist</div>
    </div>
    <div class="member" style="left:110px;top:640px">
      <div class="member__hex" style="background:var(--red)"><div class="member__photo" role="img" aria-label="Portrait of practice manager"></div></div>
      <div class="member__name">Sandra Holloway</div><div class="member__role">Practice Manager</div>
    </div>
    <div class="member" style="left:200px;top:668px">
      <div class="member__hex" style="background:var(--blue)"><div class="member__photo" role="img" aria-label="Portrait of front office administrator"></div></div>
      <div class="member__name">Nicole Brandt</div><div class="member__role">Front Office Administrator</div>
    </div>
  </section>

</main>
</body>
</html>
```